indépendant en tant que Massothérapeute et Préparateur Mental, j'ai besoin de ...

Massothérapeute et préparateur mental indépendant, je recherche une carte de visite sobre et dynamique, sans images liées au massage ou à la préparation mentale mais intégrant mon logo. Les couleurs que j'aime bien sont : Blanc, gris, anthracite, noir et jaune

Contact Information for Business Card

carte de préférence Horizontale
neutre qui puisse toucher le deux domaines Massothérapie et préparation mentale

Requirements
Must have
• mon projet doit intégrer au recto:
LOGO
Loïc Bardèze
078 513 26 48
info@loicbardeze.ch
et éventuellement www.loicbardeze.ch

et au verso les deux adresses:

Chemin des Ormilles 7B
1400 Yverdon-les-Bains

Route de la Gravière 9
1700 Fribourg

Should not have
• mon projet ne doit pas contenir d'image en liens avec le massage ni la préparation mentale.

```html
<!DOCTYPE html>
<html lang="fr">
<head>
<meta charset="utf-8">
<title>Loïc Bardèze – Carte de visite</title>
<link rel="stylesheet" href="https://fonts.googleapis.com/css2?family=Work+Sans:wght@400;500;600&display=swap">
<style>
  :root {
    --backdrop: #161616;
    --card: #262626;
    --card-light: #2e2e2e;
    --white: #ffffff;
    --text: #e9e9e9;
    --yellow: #f6bd16;
  }
  * { box-sizing: border-box; margin: 0; padding: 0; }
  html, body {
    width: 1200px; height: 900px; overflow: hidden;
    background: var(--backdrop);
    font-family: "Work Sans", sans-serif;
  }
  .stage {
    width: 1200px; height: 900px;
    display: flex; flex-direction: column;
    align-items: center; justify-content: center; gap: 40px;
  }
  .card {
    position: relative;
    width: 700px; height: 400px;
    background: linear-gradient(135deg, var(--card) 0%, var(--card-light) 70%, var(--card) 100%);
    border-bottom: 6px solid var(--yellow);
    box-shadow: 0 14px 30px rgba(0,0,0,.55);
  }
  .brand { display: flex; flex-direction: column; color: var(--white); }
  .brand-line { display: flex; align-items: center; gap: 14px; }
  .brand-mark { width: 18px; height: 18px; background: var(--white); }
  .brand-name {
    font-weight: 600; text-transform: uppercase; letter-spacing: .06em;
  }
  .brand-tagline {
    font-size: 10px; font-weight: 500; text-transform: uppercase;
    letter-spacing: .12em; color: var(--text); margin-top: 6px;
  }
  .card-front .brand {
    position: absolute; left: 50%; top: 50%;
    transform: translate(-50%, -55%); align-items: flex-start;
  }
  .card-front .brand-name { font-size: 34px; }
  .card-front .brand-mark { width: 26px; height: 26px; }
  .card-front .brand-tagline { font-size: 12px; margin-left: 40px; }

  .card-back .brand { position: absolute; left: 46px; top: 170px; }
  .card-back .brand-name { font-size: 24px; }
  .card-back .brand-tagline { margin-left: 32px; font-size: 9px; }
  .divider {
    position: absolute; left: 380px; top: 70px;
    width: 2px; height: 250px; background: var(--yellow);
  }
  .contact { position: absolute; left: 410px; top: 68px; color: var(--text); }
  .contact-name {
    color: var(--yellow); font-size: 28px; font-weight: 500;
    letter-spacing: .04em; line-height: 1;
  }
  .contact-role { font-size: 17px; margin: 6px 0 12px; }
  .contact-list { list-style: none; font-size: 17px; line-height: 1.45; }
  .contact-list li { display: flex; align-items: center; gap: 8px; }
  .contact-list svg { width: 13px; height: 13px; flex: none; }
  .address { font-style: normal; font-size: 17px; line-height: 1.35; margin-top: 10px; }
  .address + .address { margin-top: 6px; }
</style>
</head>
<body>
<main class="stage">
  <section class="card card-front" aria-label="Recto">
    <div class="brand">
      <div class="brand-line">
        <span class="brand-mark"></span>
        <span class="brand-name">Loïc Bardèze</span>
      </div>
      <span class="brand-tagline">Massothérapeute / Préparateur Mental</span>
    </div>
  </section>

  <section class="card card-back" aria-label="Verso">
    <div class="brand">
      <div class="brand-line">
        <span class="brand-mark"></span>
        <span class="brand-name">Loïc Bardèze</span>
      </div>
      <span class="brand-tagline">Massothérapeute / Préparateur Mental</span>
    </div>
    <div class="divider"></div>
    <div class="contact">
      <h1 class="contact-name">LOÏC BARDÈZE</h1>
      <p class="contact-role">Director</p>
      <ul class="contact-list">
        <li>
          <svg viewBox="0 0 16 16" aria-hidden="true"><path fill="var(--yellow)" d="M4 1l3 3-2 2c1 2 3 4 5 5l2-2 3 3-2 3C7 15 1 9 1 3z"/></svg>
          078 513 26 48
        </li>
        <li>
          <svg viewBox="0 0 16 16" aria-hidden="true"><rect x="1.5" y="3.5" width="13" height="9" fill="none" stroke="var(--yellow)" stroke-width="1.6"/><path d="M1.5 3.5l6.5 5 6.5-5" fill="none" stroke="var(--yellow)" stroke-width="1.6"/></svg>
          info@loicbardeze.ch
        </li>
        <li>
          <svg viewBox="0 0 16 16" aria-hidden="true"><g fill="none" stroke="var(--yellow)" stroke-width="1.4"><circle cx="8" cy="8" r="6.5"/><ellipse cx="8" cy="8" rx="3" ry="6.5"/><path d="M1.5 8h13M3 4.5h10M3 11.5h10"/></g></svg>
          www.loicbardeze.ch
        </li>
      </ul>
      <address class="address">Chemin des Ormilles 7B<br>1400 Yverdon-les-Bains</address>
      <address class="address">Route de la Gravière 9<br>1700 Fribourg</address>
    </div>
  </section>
</main>
</body>
</html>
```